Unravelling Markets - Podcast Cover

Unravelling Markets is a weekly podcast that dispels some of the myths about conventional economic thinking and provides a new way of thinking about issues that are faced by the global economy. It's insightful, thought-provoking and, most importantly, fun. We are refreshing the look and sound of the podcast. I have attached a copy of the old amateur design (which I did!)

Target Market(s)

Male oriented, smart folk with an interest in politics and economics

Font styles to use
Sans Serif

Requirements
Must have
• Clearly visible title, even when reduced in size. Must be 3000 pixels by 3000 pixels.
Nice to have
• This podcast challenges the status quo. It should reflect that. Photos and names of the hosts. Actually, because th ephotos are so different, we'd be open to the idea of a caricature if you can do that within the price.

```html
<!DOCTYPE html>
<html lang="en">
<head>
<meta charset="utf-8">
<title>Unravelling Markets Podcast – Cover</title>
<link rel="stylesheet" href="https://fonts.googleapis.com/css2?family=Roboto:wght@900&family=Montserrat:wght@500&display=swap">
<style>
  :root {
    --backdrop: #7a7a7a;
    --cover-white: #ffffff;
    --brand-red: #e31b23;
    --ink-black: #0a0a0a;
    --pig-pink: #f2b6c4;
    --cash-green: #9aa88e;
    --skin-tone: #d9a892;
    --shirt-white: #ecebe6;
  }
  * { margin: 0; padding: 0; box-sizing: border-box; }
  html, body {
    width: 1200px; height: 904px; overflow: hidden;
    background: var(--backdrop);
  }
  .cover {
    position: absolute; left: 170px; top: 22px;
    width: 860px; height: 860px;
    background: var(--cover-white);
    overflow: hidden;
  }
  .cover-frame {
    position: absolute; left: 39px; top: 39px; right: 39px; bottom: 39px;
    border: 2px solid var(--brand-red);
  }
  .title {
    position: absolute; left: 84px; top: 72px;
    font-family: "Roboto", Arial, sans-serif; font-weight: 900;
    line-height: 0.88; text-transform: uppercase;
  }
  .title span { display: block; }
  .title-the { font-size: 86px; color: var(--ink-black); }
  .title-main-red { font-size: 100px; color: var(--brand-red); letter-spacing: -2px; margin-top: 8px; }
  .title-main-black { font-size: 112px; color: var(--ink-black); letter-spacing: -1px; margin-top: 6px; }
  .title-podcast { font-size: 86px; color: var(--brand-red); margin-top: 8px; }
  .artwork-savings {
    position: absolute; left: 63px; top: 469px; width: 420px; height: 285px;
    background: radial-gradient(ellipse at 55% 65%, var(--pig-pink) 0%, #f7d3dc 40%, rgba(255,255,255,0) 72%),
                radial-gradient(ellipse at 30% 30%, var(--cash-green) 0%, rgba(255,255,255,0) 55%);
  }
  .host-portrait {
    position: absolute; left: 462px; top: 370px; width: 398px; height: 490px;
    background: linear-gradient(180deg, rgba(255,255,255,0) 0%, var(--skin-tone) 10%, #cf9a86 45%, var(--shirt-white) 60%, #dcdad3 100%);
    border-radius: 48% 48% 0 0 / 30% 30% 0 0;
  }
  .host-name {
    position: absolute; left: 84px; top: 758px;
    font-family: "Montserrat", Arial, sans-serif; font-weight: 500;
    font-size: 29px; letter-spacing: 1px; color: var(--ink-black);
    text-transform: uppercase;
  }
</style>
</head>
<body>
  <main class="cover">
    <div class="cover-frame"></div>
    <h1 class="title">
      <span class="title-the">The</span>
      <span class="title-main-red">Unravelling</span>
      <span class="title-main-black">Markets</span>
      <span class="title-podcast">Podcast</span>
    </h1>
    <div class="artwork-savings" role="img" aria-label="Photo of a smashed pink piggy bank with crumpled banknotes spilling out"></div>
    <div class="host-portrait" role="img" aria-label="Photo of the host, a grey-haired man in glasses and a white T-shirt"></div>
    <p class="host-name">Prof Alan Mercer</p>
  </main>
</body>
</html>
```